Our new beauty salon requires a price list brochure

Our beauty clinic is a medical grade skin care clinic. So our salon is very clinical and professional in appearance. I would like the colours to be similar to our logo design with some nice texture or abstract shapes thrown in.
Pricelist, contact details and logo is attached
I would prefer it to be a 3 fold brochure.

Target Market(s)

Females aged 30-50

Colors
85acd3
cedeed
c4c4c4
5c5c5c
000000
ffffff
eea3c7
f9d9e8
dbdbdb

Requirements
Must have
• easy to read

```html
<!DOCTYPE html>
<html lang="en">
<head>
<meta charset="utf-8">
<title>Lumen Aesthetics – Services Menu</title>
<link href="https://fonts.googleapis.com/css2?family=Cabin:wght@400;700&family=Parisienne&display=swap" rel="stylesheet">
<style>
  :root{
    --pink:#eea3c7;
    --pink-soft:#f9d9e8;
    --pink-line:#f3c6da;
    --ink:#5c5c5c;
    --slate:#4e5466;
    --slate-line:#7d8191;
    --panel:#a5a7b6;
    --white:#ffffff;
  }
  *{margin:0;padding:0;box-sizing:border-box}
  html,body{width:1200px;height:848px;overflow:hidden;background:var(--white)}
  body{font-family:"Cabin",sans-serif;color:var(--ink)}
  .sheet{position:relative;width:1200px;height:848px;overflow:hidden;background:var(--white)}

  .portrait-wash{
    position:absolute;left:440px;top:0;width:760px;height:848px;
    background:
      radial-gradient(ellipse 420px 520px at 560px 260px, rgba(249,217,232,.85), rgba(249,217,232,0) 70%),
      radial-gradient(ellipse 300px 360px at 300px 620px, rgba(249,217,232,.55), rgba(249,217,232,0) 70%),
      radial-gradient(ellipse 260px 300px at 720px 90px, rgba(238,163,199,.35), rgba(238,163,199,0) 70%);
  }
  .base-strip{position:absolute;left:0;top:828px;width:1200px;height:16px;
    background:linear-gradient(90deg,rgba(249,217,232,.2),var(--pink-soft) 40%,rgba(249,217,232,.6))}

  .menu-title{position:absolute;left:24px;top:34px;font-family:"Parisienne",cursive;
    font-size:40px;line-height:40px;color:var(--pink-line);letter-spacing:1px}
  .title-rule{position:absolute;left:24px;right:0;top:83px;border-top:2px dotted var(--pink-soft)}

  .section-head{position:absolute;width:322px;padding-left:19px;padding-bottom:5px;
    font-size:11.5px;line-height:14px;font-weight:700;letter-spacing:1.6px;text-transform:uppercase;
    color:var(--pink);border-bottom:2px solid var(--pink-soft)}
  .section-head.is-slate{color:var(--slate);border-bottom:1.5px solid var(--slate-line);width:323px}

  .price-list{position:absolute;font-size:11.5px;line-height:19.45px}
  .price-list::after{content:"";position:absolute;left:215px;top:-8px;bottom:-8px;border-left:1.5px dotted #9a9a9a}
  .row{display:flex;white-space:nowrap}
  .row .name{width:243px}
  .spacer{height:19.45px;position:relative}
  .spacer::before{content:"";position:absolute;top:9px;border-top:1.5px dotted #9a9a9a}
  .spacer.wide::before{left:-19px;width:193px}
  .spacer.short::before{left:0;width:174px}

  .treatment{position:absolute;left:844px;width:323px;height:21px;padding-left:19px;
    border-bottom:1.5px solid var(--slate-line);display:flex;font-size:11.5px;line-height:16px}
  .treatment .name{width:243px;font-weight:700;letter-spacing:1.6px;color:var(--slate);text-transform:uppercase}
  .treatment .duration{font-style:italic;margin-left:6px}
  .treatment-divider{position:absolute;left:1079px;top:283px;height:147px;border-left:1px solid #b9bcc6}

  .note{position:absolute;left:863px;font-size:11.5px;line-height:15px}

  .contact-panel{position:absolute;left:462px;top:727px;width:721px;height:101px;background:var(--panel);
    border-radius:0 34px 0 0}
  .brand-name{position:absolute;left:74px;top:32px;font-size:26px;line-height:34px;font-weight:400;
    letter-spacing:4px;color:var(--white);text-transform:lowercase}
  .contact{position:absolute;left:400px;top:26px;width:280px;text-align:center;color:var(--white);
    font-size:16px;line-height:23px;letter-spacing:1.2px}
</style>
</head>
<body>
<main class="sheet">
  <div class="portrait-wash" role="img" aria-label="Soft-focus portrait of a woman in pale pink tones"></div>
  <div class="base-strip"></div>

  <h1 class="menu-title">services menu</h1>
  <div class="title-rule"></div>

  <!-- Column one -->
  <h2 class="section-head" style="left:61px;top:118px">IPL Hair Removal</h2>
  <div class="price-list" style="left:80px;top:155px">
    <div class="row"><span class="name">Upper lip</span><span>$50</span></div>
    <div class="row"><span class="name">Chin</span><span>$50</span></div>
    <div class="row"><span class="name">Cheeks</span><span>$75</span></div>
    <div class="row"><span class="name">Whole face</span><span>$350</span></div>
    <div class="spacer wide"></div>
    <div class="row"><span class="name">Bikini</span><span>$90</span></div>
    <div class="row"><span class="name">G String</span><span>$120</span></div>
    <div class="row"><span class="name">Brazilian</span><span>$150</span></div>
    <div class="spacer wide"></div>
    <div class="row"><span class="name">Underarms</span><span>$90</span></div>
    <div class="row"><span class="name">Half arm</span><span>$180</span></div>
    <div class="row"><span class="name">Full arm</span><span>$250</span></div>
    <div class="row"><span class="name">Half leg</span><span>$290</span></div>
    <div class="row"><span class="name">Thighs</span><span>$290</span></div>
    <div class="row"><span class="name">Full leg</span><span>$490</span></div>
    <div class="spacer wide"></div>
    <div class="row"><span class="name">Full back</span><span>$350</span></div>
    <div class="row"><span class="name">Shoulders</span><span>$180</span></div>
    <div class="row"><span class="name">Nipples</span><span>$60</span></div>
    <div class="row"><span class="name">Snail trail</span><span>$50</span></div>
    <div class="row"><span class="name">Stomach</span><span>$250</span></div>
    <div class="row"><span class="name">Chest</span><span>$250</span></div>
    <div class="row"><span class="name">Buttocks</span><span>$200</span></div>
  </div>

  <h2 class="section-head" style="left:61px;top:643px">IPL Photo Rejuvenation</h2>
  <div class="price-list" style="left:80px;top:679px">
    <div class="row"><span class="name">Full face</span><span>$350</span></div>
    <div class="row"><span class="name">Neck</span><span>$200</span></div>
    <div class="row"><span class="name">Face, neck ad décolletage</span><span>$450</span></div>
    <div class="row"><span class="name">Spot Treatment</span><span>$50</span></div>
  </div>

  <!-- Column two -->
  <h2 class="section-head" style="left:465px;top:118px">Waxing</h2>
  <div class="price-list" style="left:484px;top:155px">
    <div class="row"><span class="name">Eyebrow</span><span>$21</span></div>
    <div class="row"><span class="name">Lip</span><span>$15</span></div>
    <div class="row"><span class="name">Chin</span><span>$15</span></div>
    <div class="row"><span class="name">Sides of face</span><span>$20</span></div>
    <div class="row"><span class="name">Underarm</span><span>$20</span></div>
    <div class="row"><span class="name">Forearm</span><span>$25</span></div>
    <div class="row"><span class="name">Full arm</span><span>$35</span></div>
    <div class="row"><span class="name">Lower leg</span><span>$30</span></div>
    <div class="row"><span class="name">Upper leg</span><span>$30</span></div>
    <div class="row"><span class="name">Full leg</span><span>$50</span></div>
    <div class="row"><span class="name">Inner thigh</span><span>$10</span></div>
    <div class="row"><span class="name">Snail trail</span><span>$10</span></div>
    <div class="row"><span class="name">Bikini</span><span>$30</span></div>
    <div class="row"><span class="name">G String</span><span>$40</span></div>
    <div class="row"><span class="name">Brazilian</span><span>$50</span></div>
    <div class="spacer short"></div>
    <div class="row"><span class="name">Eyebrow wax and Lip wax</span><span>$30</span></div>
    <div class="row"><span class="name">Eyebrow, lip and chin wax</span><span>$45</span></div>
  </div>

  <h2 class="section-head" style="left:465px;top:546px">Mens Waxing</h2>
  <div class="price-list" style="left:484px;top:582px">
    <div class="row"><span class="name">Mono brow</span><span>$5</span></div>
    <div class="row"><span class="name">Eyebrow</span><span>$21</span></div>
    <div class="row"><span class="name">Neck</span><span>$20</span></div>
    <div class="row"><span class="name">Full back</span><span>$45</span></div>
    <div class="row"><span class="name">Chest and Abdomen</span><span>$45</span></div>
  </div>

  <!-- Column three -->
  <h2 class="section-head is-slate" style="left:844px;top:118px">Tinting</h2>
  <div class="price-list" style="left:863px;top:155px">
    <div class="row"><span class="name">Eyelash Tint</span><span>$25</span></div>
    <div class="row"><span class="name">Lash Lift and Tint</span><span>$80</span></div>
    <div class="spacer short"></div>
    <div class="row"><span class="name">Henna eyebrows and wax</span><span>$80</span></div>
    <div class="row"><span class="name">Eyelash Tint and brow wax</span><span>$40</span></div>
  </div>

  <div class="treatment-divider"></div>
  <div class="treatment" style="top:293px"><span class="name">Lumen Mini Facial</span><span>$80</span><span class="duration">40min</span></div>
  <div class="treatment" style="top:333px"><span class="name">Lumen Deluxe Facial</span><span>$110</span><span class="duration">1hr</span></div>
  <div class="treatment" style="top:371px"><span class="name">Microdermabrasion</span><span>$125</span></div>
  <div class="treatment" style="top:410px"><span class="name">Mini Micro</span><span>$80</span></div>

  <h2 class="section-head is-slate" style="left:844px;top:469px">Wrinkle Relaxers</h2>
  <p class="note" style="top:507px">$175 per area (Crows, frown lines, forehead lines) <em>or</em><br>all 3 areas for $450<br>$50 minor areas (Gummy smile, brow lift, bunny lines)</p>

  <h2 class="section-head is-slate" style="left:844px;top:597px">Dermal Fillers and Lip Fillers</h2>
  <p class="note" style="top:636px">$500 per ml</p>

  <!-- Contact -->
  <footer class="contact-panel">
    <div class="brand-name">lumen aesthetics</div>
    <div class="contact">(08) 9000 1234<br>lumenaesthetics.com.au</div>
  </footer>
</main>
</body>
</html>
```